Emerging automotive detailing business

I am starting a small automotive detailing business in hopes of becoming a well-known detailer to work on high end cars. I would like a card to reflect the high quality and time I put into my work. The name of the company is Bright Crest Detailing. I feel like it represents racecars getting off the line at the drag strip as well as an innuendo of "Up the Ladder". I do minor paint correction such as clay barring, multi-step buffing and polishing, waxing, hand washes, etc. I am always striving to learn more and improve my work. My goal is to have total customer satisfaction. This is a female run business but I do not want it to be very girly. Elegant is okay! I have pictures of my personal wrenfield attached, they do not need to be incorporated but if you can think of a cool way to use 1 or all of them, go for it!

Target Market(s)

Anyone that owns a vehicle. Preferably high end vehicles such as Valtori, Castellverde and Morvani but I will also happily work on any car, truck or suv no matter what brand.

Industry/Entity Type

Automotive

Contact Information for Business Card

Bright Crest Detailing
Mira Tolland
4175 Quenhollow Rd
Ashmere PA 17492
Cell phone- call/text- 717-555-0148
email- brightcrestdetails@maildrop-example.com
Instagram: @brightcrestdetailing
Facebook: facebook.com/brightcrestdetailing

Requirements
Must have
• Business name, my name, address, phone number. Listing that I do minor paint correction such as clay barring, multi-step buffing and polishing, waxing, hand washes, interior cleaning, and more. (This last part was in nice to haves but I have realized that I do really want it, so I moved it to must haves.) I want something that is different and eye-catching to my customers. Some people have done this very well with cards already submitted to me, but a lot have not. I didn't mess with the "look and feel bars" much because because I am pretty open to the overall design as long as it is not your basic run of the mill design.
Nice to have
• Something car related. Maybe an appointment time/date line. I do not have a logo, but if you would like to design one and incorporate it, that would be amazing!
Should not have
• Purple and Pink colors. Boring, basic, normal card.

```html
<!DOCTYPE html>
<html lang="en">
<head>
<meta charset="utf-8">
<title>Bright Crest Detailing – Business Card</title>
<link href="https://fonts.googleapis.com/css2?family=Lato:wght@300;400;700&family=Poiret+One&display=swap" rel="stylesheet">
<style>
  :root {
    --page-bg: #2b2420;
    --card-black: #0b0b0b;
    --photo-deep: #1c211a;
    --photo-mid: #3d4630;
    --photo-car: #6f6a2c;
    --band-cream: #fde995;
    --band-edge: #e9d27a;
    --ink-dark: #1a1a1a;
    --ink-soft: #5a5132;
    --service-text: #f3e7a6;
    --bullet-red: #d8232a;
    --gold-text: #e8d58a;
  }
  * { margin: 0; padding: 0; box-sizing: border-box; }
  html, body {
    width: 1200px;
    height: 1023px;
    overflow: hidden;
    background: var(--page-bg);
    font-family: "Lato", sans-serif;
  }
  .stage {
    width: 1200px;
    height: 1023px;
    display: flex;
    flex-direction: column;
    align-items: center;
    justify-content: center;
    gap: 40px;
  }
  .card {
    position: relative;
    width: 770px;
    height: 440px;
    background: var(--card-black);
    overflow: hidden;
    box-shadow: 0 14px 32px rgba(0,0,0,0.45);
  }

  /* Front */
  .card__photo {
    position: absolute;
    left: 0;
    top: 0;
    width: 100%;
    height: 275px;
    background:
      linear-gradient(to bottom, var(--card-black) 0%, rgba(11,11,11,0.55) 22%, rgba(11,11,11,0.15) 55%, rgba(11,11,11,0.6) 100%),
      radial-gradient(ellipse 38% 55% at 52% 70%, var(--photo-car) 0%, rgba(111,106,44,0) 100%),
      linear-gradient(to right, var(--photo-deep) 0%, var(--photo-mid) 45%, #4a4c46 75%, var(--photo-deep) 100%);
  }
  .card__services {
    position: absolute;
    left: 14px;
    top: 196px;
    color: var(--service-text);
    font-size: 20px;
    font-weight: 400;
    line-height: 1.3;
    z-index: 2;
  }
  .card__services-row { white-space: nowrap; }
  .card__services-row--upper { padding-left: 100px; }
  .service::before {
    content: "";
    display: inline-block;
    width: 6px;
    height: 6px;
    border-radius: 50%;
    background: var(--bullet-red);
    margin: 0 6px 4px 6px;
    vertical-align: middle;
  }
  .card__band {
    position: absolute;
    left: 0;
    bottom: 0;
    width: 100%;
    height: 165px;
    background: var(--band-cream);
    border-top: 2px solid var(--band-edge);
  }
  .appointment__title {
    position: absolute;
    left: 44px;
    top: 108px;
    color: var(--ink-dark);
    font-size: 20px;
    font-weight: 400;
  }
  .appointment__field {
    position: absolute;
    top: 30px;
    color: var(--ink-soft);
    font-size: 19px;
    font-weight: 300;
  }
  .appointment__field--date { left: 300px; }
  .appointment__field--time { left: 565px; }

  /* Back */
  .card--back {
    display: flex;
    flex-direction: column;
    align-items: center;
    justify-content: center;
    text-align: center;
    color: var(--gold-text);
  }
  .brand-name {
    font-family: "Poiret One", sans-serif;
    font-size: 44px;
    letter-spacing: 5px;
    text-transform: uppercase;
    font-weight: 400;
  }
  .owner-name {
    margin-top: 14px;
    font-size: 20px;
    font-weight: 400;
    letter-spacing: 2px;
  }
  .contact {
    margin-top: 26px;
    font-size: 15px;
    font-weight: 300;
    line-height: 1.6;
    font-style: normal;
  }
</style>
</head>
<body>
  <main class="stage">
    <section class="card card--front" aria-label="Bright Crest Detailing appointment side">
      <div class="card__photo" role="img" aria-label="Photo of a yellow sports car parked among other cars, darkened"></div>
      <div class="card__services">
        <div class="card__services-row card__services-row--upper">
          <span class="service">Multi-step buffing and polishing</span>
        </div>
        <div class="card__services-row">
          <span class="service">Clay barring</span><span class="service">Hand washes</span><span class="service">Waxing</span><span class="service">Interior cleaning and more</span>
        </div>
      </div>
      <div class="card__band">
        <span class="appointment__title">Appointment</span>
        <span class="appointment__field appointment__field--date">Date</span>
        <span class="appointment__field appointment__field--time">Time</span>
      </div>
    </section>

    <section class="card card--back" aria-label="Bright Crest Detailing contact side">
      <h1 class="brand-name">Bright Crest Detailing</h1>
      <p class="owner-name">Mira Tolland</p>
      <address class="contact">
        4175 Quenhollow Rd, Ashmere PA 17492<br>
        Call/Text: 717-555-0148<br>
        brightcrestdetails@maildrop-example.com<br>
        Instagram: @brightcrestdetailing<br>
        facebook.com/brightcrestdetailing
      </address>
    </section>
  </main>
</body>
</html>
```